Meal Plan Website Needs New Pages Designed

Brightwick Supper Kits is an online, membership based program that delivers weekly meal programs (7 days worth of recipes plus shopping lists) carefully crafted by an expert team of meal planners. All recipes are created to comply with the following macronutrient ratio: 65% healthy fats, 25% lean protein, 10% good carbs.
All recipes are Paleo friendly and a great resource for those individuals who want to correctly implement this type of diet.

We are re-designing our website and need the following pages designed:

· Home page w/ logo
· How it works page
· Get Started! page
· Recipes Page template (these will be the pages on our site that will have recipes)
· Kitchen Essentials Training page (this will be a page with videos and tips + tricks, PDFs, etc)

So 5 total PSDs, 1 for each page.

Target audience: Men and women between the ages of 30 and 60 who want to:
· Eat healthy
· Lose weight
· Follow/Implement the Paleo diet
· Take the guesswork out of preparing delicious AND healthy meals for them and their families
· Know exactly what to eat, what to buy, how to make it

Feelings/Messages we want to communicate through the design:
· “Organic” but elegant look
· Fresh/light/Airy
· Simple but NOT GENERIC
· “I want to get cooking” feeling

Our Stylistic preferences:
· Minimalist with a few bold elements (something in between)
· Easy to visually navigate (enough white space, but not too much)
· There is more to “see” than to “read”

Our Color Preferences:
· Lighter pallet
· Colors that evoke natural woods, granite countertops…
· Stay away from using all dark colors

Our Font Type Preferences:
· Easy to read
· Not more than 3 font types
· Not too rigid
· Not too sophisticated
· Simple with a touch

Examples of Website Designs that we like:
· http://www.dorvanta.com/meal-plans/
· http://grulvix.com/
· https://www.mistobarn.com/

```html
<!DOCTYPE html>
<html lang="en">
<head>
<meta charset="utf-8">
<title>Brightwick Supper Kits — Weekly Meal Programs</title>
<link rel="stylesheet" href="https://fonts.googleapis.com/css2?family=Oswald:wght@300;400&family=Lato:wght@400;700&display=swap">
<style>
:root{
  --red:#d0101b;
  --red-dark:#b30c16;
  --ink:#4a3b36;
  --body:#6b625c;
  --sand:#ece6da;
  --card:#ecdfcd;
  --card-edge:#dccdb7;
  --paper:#fbfaf4;
  --white:#ffffff;
}
*{box-sizing:border-box;margin:0;padding:0}
html,body{width:1200px;height:2161px;overflow:hidden}
body{position:relative;background:var(--sand);font-family:'Lato',sans-serif;color:var(--body)}
.abs{position:absolute}
.heading{font-family:'Oswald',sans-serif;font-weight:400;color:var(--red)}

/* header */
.site-header{left:0;top:0;width:1200px;height:192px;background:var(--sand)}
.brand{left:94px;top:0;width:171px;height:158px;background:linear-gradient(#fdfcf8,#f1ece2);border:1px solid #d8d0c2;border-top:none;box-shadow:0 2px 3px rgba(0,0,0,.12);display:flex;align-items:center;justify-content:center;text-align:center;padding:0 12px}
.brand-name{font-weight:700;font-size:16px;line-height:1.3;color:var(--red);text-transform:uppercase}
.brand-dot{left:168px;top:150px;width:22px;height:22px;border-radius:50%;background:var(--red)}
.social{display:flex;gap:4px}
.social span{width:37px;height:37px;border-radius:50%;background:var(--red);display:block}
.social-top{left:932px;top:42px}
.main-nav{left:465px;top:112px;width:625px;height:46px;display:flex;background:var(--white);box-shadow:0 3px 5px rgba(0,0,0,.15)}
.main-nav a{flex:1;display:flex;align-items:center;justify-content:center;font-size:17px;color:var(--red);text-decoration:none;text-transform:uppercase}
.main-nav a.active{background:var(--red);color:var(--white);flex:0 0 162px}

/* hero */
.hero{left:0;top:192px;width:1200px;height:355px;background:var(--paper)}
.hero-photo{left:184px;top:21px;width:212px;height:334px;background:linear-gradient(180deg,#f4f1ec 0%,#e9e4dd 40%,#d8242c 60%,#c5161e 100%);border-radius:90px 90px 0 0}
.hero-kicker{left:445px;top:82px;font-family:'Oswald',sans-serif;font-weight:300;font-size:29px;color:var(--ink)}
.hero-title{left:443px;top:124px;font-family:'Oswald',sans-serif;font-weight:400;font-size:60px;color:var(--ink);letter-spacing:-.5px}
.hero-title b{color:var(--red);font-weight:400}
.hero-ratio{left:445px;top:212px;font-family:'Oswald',sans-serif;font-size:28px;color:var(--red)}
.hero-arrow{top:140px;width:42px;height:42px;border-radius:50%;background:var(--white);box-shadow:0 1px 4px rgba(0,0,0,.12)}
.hero-arrow svg{display:block;margin:13px auto 0}

/* features */
.features{left:0;top:547px;width:1200px;height:520px;background:var(--sand)}
.feature{top:32px;width:313px;height:450px;background:var(--card);border:2px solid var(--card-edge);box-shadow:0 2px 4px rgba(0,0,0,.1);text-align:center}
.feature-icon{width:118px;height:118px;border-radius:50%;background:var(--paper);box-shadow:0 3px 6px rgba(0,0,0,.15);margin:38px auto 0;display:flex;align-items:center;justify-content:center}
.feature-title{font-size:29px;margin-top:30px;text-transform:uppercase;letter-spacing:-.3px}
.feature-text{font-size:17px;line-height:31px;margin:14px 26px 0}
.btn{display:inline-block;background:var(--red);color:var(--white);font-size:16px;padding:0 20px;height:42px;line-height:42px;border-radius:3px;margin-top:26px}

/* why */
.why{left:0;top:1067px;width:1200px;height:270px;background:var(--paper)}
.why-title{left:109px;top:70px;font-size:29px}
.why-text{left:111px;top:127px;width:660px;font-size:17px;line-height:31px}
.why-photo{left:825px;top:16px;width:183px;height:254px;background:linear-gradient(180deg,#ffffff 0%,#efe9e2 35%,#6d4a35 55%,#f2efea 75%,#e6e1da 100%);border-radius:80px 80px 0 0}

/* gallery */
.gallery{left:0;top:1337px;width:1200px;height:258px;background:var(--sand)}
.tile{top:42px;width:230px;height:175px}
.tile-classic{background:linear-gradient(135deg,#e2464c,#c9242a);text-align:center;color:var(--white);font-family:'Oswald',sans-serif}
.tile-classic .t1{font-size:27px;margin-top:38px}
.tile-classic .t2{font-size:20px;margin-top:4px}
.tile-classic .t3{font-size:14px;margin-top:16px;opacity:.85}

/* team */
.team{left:0;top:1595px;width:1200px;height:357px;background:var(--paper)}
.team-title{left:0;top:20px;width:1200px;text-align:center;font-size:29px}
.quote{top:105px;width:480px;height:147px;background:var(--card);border:2px solid var(--card-edge);box-shadow:0 2px 4px rgba(0,0,0,.1)}
.quote::after{content:"";position:absolute;left:230px;bottom:-14px;border:12px solid transparent;border-top-color:var(--card-edge);border-bottom:0}
.avatar{left:36px;top:25px;width:94px;height:94px;border-radius:50%;background:radial-gradient(circle at 50% 40%,#e7d4c6,#8a6a58);border:3px solid var(--white)}
.quote p{position:absolute;left:153px;top:24px;width:305px;font-size:14.5px;line-height:31px;color:#5a514b}
.person{top:268px;width:480px;text-align:center}
.person .name{font-size:19px;color:#4b4440}
.person .role{font-size:14px;margin-top:10px;color:#5a514b}

/* signup footer */
.signup{left:0;top:1952px;width:1200px;height:209px;background:var(--sand)}
.signup-title{left:109px;top:20px;font-size:29px;text-transform:uppercase;letter-spacing:-.3px}
.field{top:82px;width:232px;height:51px;background:var(--white);font-family:'Oswald',sans-serif;font-size:15px;color:#8a7e74;padding-left:12px;line-height:51px}
.submit{left:612px;top:82px;width:130px;height:51px;background:var(--red);color:var(--white);font-family:'Oswald',sans-serif;font-size:16px;text-align:center;line-height:51px}
.social-foot{left:946px;top:89px}
.rule{left:0;top:154px;width:1200px;height:1px;background:#d9d0c2}
.foot-links{left:109px;top:172px;font-family:'Oswald',sans-serif;font-size:15px;color:#8f847a;word-spacing:8px}
.copyright{right:99px;top:172px;font-family:'Oswald',sans-serif;font-size:15px;color:#8f847a;text-transform:uppercase}
</style>
</head>
<body>

<header class="site-header abs">
  <div class="brand abs"><span class="brand-name">Brightwick Supper Kits</span></div>
  <span class="brand-dot abs"></span>
  <div class="social social-top abs" aria-label="Social links"><span></span><span></span><span></span><span></span></div>
  <nav class="main-nav abs">
    <a class="active" href="#">Meal Plans</a>
    <a href="#">About</a>
    <a href="#">How it works</a>
    <a href="#">Resources</a>
  </nav>
</header>

<section class="hero abs">
  <div class="hero-arrow abs" style="left:28px"><svg width="16" height="16" viewBox="0 0 16 16"><path d="M8 3 3 8l5 5M13 3 8 8l5 5" fill="none" stroke="#777" stroke-width="1.6"/></svg></div>
  <div class="hero-photo abs" role="img" aria-label="Smiling chef in white jacket and red apron presenting a silver cloche"></div>
  <p class="hero-kicker abs">We provide membership based program that delivers</p>
  <h1 class="hero-title abs">WEEKLY <b>MEAL</b> PROGRAMS</h1>
  <p class="hero-ratio abs">65% HEALTHY FATS,&nbsp; 25% LEAN PROTEIN,&nbsp; 10% GOOD CARBS</p>
  <div class="hero-arrow abs" style="left:1123px"><svg width="16" height="16" viewBox="0 0 16 16"><path d="M8 3l5 5-5 5M3 3l5 5-5 5" fill="none" stroke="#777" stroke-width="1.6"/></svg></div>
</section>

<section class="features abs">
  <article class="feature abs" style="left:109px">
    <div class="feature-icon"><svg width="70" height="60" viewBox="0 0 70 60"><path d="M22 6c-4 4 4 7 0 11M34 2c-4 4 4 8 0 13M46 6c-4 4 4 7 0 11" fill="none" stroke="var(--red)" stroke-width="3"/><path d="M5 28h60c-2 13-12 20-30 20S7 41 5 28z" fill="none" stroke="var(--red)" stroke-width="4"/><path d="M18 52h34" stroke="var(--red)" stroke-width="4"/></svg></div>
    <h2 class="feature-title heading">Meal Plans</h2>
    <p class="feature-text">Weekly Paleo meal plans—including recipes and shopping lists—sent straight to your inbox. No more wondering what's for dinner.</p>
    <span class="btn">Learn More</span>
  </article>
  <article class="feature abs" style="left:444px">
    <div class="feature-icon"><svg width="50" height="66" viewBox="0 0 50 66"><path d="M6 10 40 2v56L6 64z" fill="none" stroke="var(--red)" stroke-width="4"/><path d="M6 10h38v50H40" fill="none" stroke="var(--red)" stroke-width="4"/><path d="M14 24l18-4" stroke="var(--red)" stroke-width="3"/></svg></div>
    <h2 class="feature-title heading">Quickstart Guide</h2>
    <p class="feature-text">Weekly Paleo meal plans—including recipes and shopping lists—sent straight to your inbox. No more wondering what's for dinner.</p>
    <span class="btn">Learn More</span>
  </article>
  <article class="feature abs" style="left:776px">
    <div class="feature-icon"><svg width="70" height="62" viewBox="0 0 70 62"><path d="M8 4h54l6 16H2z" fill="var(--red)"/><path d="M6 24h58v30H6z" fill="none" stroke="var(--red)" stroke-width="5"/><rect x="18" y="30" width="34" height="18" fill="var(--red)"/><rect x="2" y="54" width="66" height="6" fill="var(--red)"/></svg></div>
    <h2 class="feature-title heading">At-Home Workouts</h2>
    <p class="feature-text">Weekly Paleo meal plans—including recipes and shopping lists—sent straight to your inbox. No more wondering what's for dinner.</p>
    <span class="btn">Learn More</span>
  </article>
</section>

<section class="why abs">
  <h2 class="why-title heading abs">Why should I eat ?</h2>
  <p class="why-text abs">About 10,000 years ago, our diets changed dramatically after nearly 2.5 million years of evolution. The Paleo diet is a return to the type of food that we were made to eat.</p>
  <div class="why-photo abs" role="img" aria-label="Chef in toque holding wooden kitchen spoons"></div>
</section>

<section class="gallery abs">
  <div class="tile tile-classic abs" style="left:109px">
    <div class="t1">CLASSIC</div>
    <div class="t2">SIMPLE AND DELICIOUS</div>
    <div class="t3">LEARN MORE</div>
  </div>
  <div class="tile abs" style="left:360px;background:radial-gradient(circle at 55% 55%,#b5742f 0%,#8fb9c4 45%,#d9cfc4 100%)" role="img" aria-label="Grilled chicken skewers on a blue plate"></div>
  <div class="tile abs" style="left:611px;background:radial-gradient(circle at 45% 55%,#e0762e 0%,#8fa43a 40%,#d9b48a 100%)" role="img" aria-label="Fresh salad with carrots and cucumber"></div>
  <div class="tile abs" style="left:861px;background:linear-gradient(135deg,#c8323a 0%,#e6cdb2 40%,#b7c27a 100%)" role="img" aria-label="Lunch box with strawberries and cucumber slices"></div>
</section>

<section class="team abs">
  <h2 class="team-title heading abs">An expert team dedicated to your success</h2>
  <figure class="quote abs" style="left:109px">
    <div class="avatar abs" role="img" aria-label="Portrait of Marla Tevens"></div>
    <p>Brightwick Supper Kits is amazing. My husband and I began three weeks ago and are losing weight and feeling much more energetic.</p>
  </figure>
  <div class="person abs" style="left:109px"><div class="name">Marla Tevens</div><div class="role">Nutrition Therapist</div></div>
  <figure class="quote abs" style="left:611px">
    <div class="avatar abs" role="img" aria-label="Portrait of Dorin Kalloway"></div>
    <p>Just wanted to let you know that my husband, son, and I have loved the recipes! They have been simple to prepare and delicious...</p>
  </figure>
  <div class="person abs" style="left:611px"><div class="name">Dorin Kalloway</div><div class="role">Iron Circuit Coach and Fitness Expert</div></div>
</section>

<footer class="signup abs">
  <h2 class="signup-title heading abs">Get a free meal plan!</h2>
  <div class="field abs" style="left:109px">ENTER YOUR NAME</div>
  <div class="field abs" style="left:360px">ENTER YOUR MAIL ID</div>
  <div class="submit abs">SUBMIT</div>
  <div class="social social-foot abs" aria-label="Social links"><span></span><span></span><span></span><span></span></div>
  <div class="rule abs"></div>
  <div class="foot-links abs">PRESS TERMS CONTACT</div>
  <div class="copyright abs">© 2014 Brightwick Supper Kits. All rights reserved.</div>
</footer>

</body>
</html>
```